Packaging design for a reclosable bag for our product

We have a logo, and we need to put it on packaging for our product and while we want the look to be simple, we want it to follow good design principles and also contain spaces for other product descriptions.

There will be 5 sizes at launch so I'd like 5 variations, one for each size.

I've included a few mockups of the type of bag that I made but they are all just rough ideas that I had.

I want the brand to look scientific and methodical and even a bit quirky, as in "wow this is a serious product but also a bit unusual."

```html
<!DOCTYPE html>
<html lang="en">
<head>
<meta charset="utf-8">
<title>Kelvo Bias Lighting – 5m Pouch</title>
<link rel="stylesheet" href="https://fonts.googleapis.com/css2?family=Ubuntu:wght@500;700&family=Nunito:wght@900&display=swap">
<style>
  :root {
    --backdrop: #3b393a;
    --foil-light: #d9d9d9;
    --foil-mid: #a9a9a9;
    --foil-dark: #8c8c8c;
    --band: #f2f2f2;
    --band-edge: #6f6f6f;
    --ink: #1b1b1b;
    --base: #050505;
    --pale: #f4f4f4;
    --pill: #5a5a5a;
  }
  * { margin: 0; padding: 0; box-sizing: border-box; }
  html, body {
    width: 1200px; height: 848px; overflow: hidden;
    background: var(--backdrop);
  }
  .canvas { position: relative; width: 1200px; height: 848px; }
  .pouch {
    position: absolute; left: 406px; top: 191px;
    width: 340px; height: 491px;
    border-radius: 3px 3px 6px 6px;
    overflow: hidden;
    background: var(--base);
  }
  .pouch__foil {
    position: absolute; left: 0; top: 0; width: 100%; height: 245px;
    background: linear-gradient(180deg, var(--foil-light) 0%, var(--foil-mid) 30%, var(--foil-light) 55%, var(--foil-dark) 100%);
  }
  .pouch__zip {
    position: absolute; left: 0; top: 55px; width: 100%; height: 6px;
    border-top: 1px solid rgba(255,255,255,.6);
    border-bottom: 1px solid rgba(0,0,0,.15);
  }
  .brand-name {
    position: absolute; left: 0; top: 98px; width: 100%;
    text-align: center;
    font-family: "Ubuntu", sans-serif; font-weight: 700;
    font-size: 96px; letter-spacing: -2px; line-height: 1;
    color: var(--pale);
  }
  .product-band {
    position: absolute; left: 0; top: 242px; width: 100%; height: 46px;
    background: var(--band);
    border-top: 4px solid var(--band-edge);
    border-bottom: 2px solid #9a9a9a;
    display: flex; align-items: center; justify-content: center;
    font-family: "Ubuntu", sans-serif; font-weight: 500;
    font-size: 29px; letter-spacing: 1px; color: var(--ink);
  }
  .size-tag {
    position: absolute; left: 150px; top: 316px;
    padding: 1px 8px; border-radius: 9px;
    background: var(--pill);
    font-family: "Ubuntu", sans-serif; font-weight: 500;
    font-size: 12.5px; letter-spacing: .5px; color: #e8e8e8;
  }
  .size-value {
    position: absolute; left: 62px; top: 318px;
    font-family: "Nunito", sans-serif; font-weight: 900;
    font-size: 128px; line-height: 1; letter-spacing: -3px;
    background: linear-gradient(180deg, #f4f4f4 0%, #bdbdbd 45%, #6e6e6e 100%);
    -webkit-background-clip: text; background-clip: text; color: transparent;
  }
  .spec-lines {
    position: absolute; left: 0; top: 430px; width: 100%;
    text-align: center;
    font-family: "Ubuntu", sans-serif; font-weight: 500;
    font-size: 14.5px; line-height: 21px; color: var(--pale);
  }
</style>
</head>
<body>
  <main class="canvas">
    <section class="pouch">
      <div class="pouch__foil"></div>
      <div class="pouch__zip"></div>
      <div class="brand-name">Kelvo</div>
      <div class="product-band">BIAS LIGHTING</div>
      <div class="size-tag">EXTRA LARGE</div>
      <div class="size-value">5m</div>
      <p class="spec-lines">6500K White Bias Lighting<br>Simulated D65 CRI 90+</p>
    </section>
  </main>
</body>
</html>
```